TK Homes - Stone Dorf Design

Looking for a double sides design, 1 side for my realestate and the other for home building. ( TK Homes on 1 side, Stone Dorf card on the other Side
Side 1 - Marek Tove ~ Vox Realty logo and Company ( the Property quarter )
Marek Tove
Marek@Marektove.example
IG - Marek_Bzq_Realtor
FB - marekt
Cell - 5558130467
3847 61 St Nw

Side 2
Marek Tove
5558130467
IG - Stonedorf_Bzq
Stonedorfdev@mailbox.example

Target Market(s)

Home buyers/ sellers

Industry/Entity Type

Home builders - Realestate

Contact Information for Business Card

Above

Requirements
Must have
• Black OR White background - my information -

```html
<!DOCTYPE html>
<html lang="en">
<head>
<meta charset="utf-8">
<title>TK Homes – Stone Dorf Design business cards</title>
<link rel="stylesheet" href="https://fonts.googleapis.com/css2?family=Tinos:wght@400;700&display=swap">
<style>
  :root {
    --page: #232325;
    --card: #1e1e22;
    --blue: #0b72bf;
    --red: #e05243;
    --white: #f4f4f4;
    --divider: rgba(255,255,255,0.85);
  }
  * { box-sizing: border-box; margin: 0; padding: 0; }
  html, body { width: 1200px; height: 780px; overflow: hidden; }
  body {
    background: var(--page);
    font-family: "Tinos", "Times New Roman", serif;
    color: var(--white);
    position: relative;
  }
  .card {
    position: absolute;
    top: 230px;
    width: 560px;
    height: 320px;
    background: var(--card);
    border-radius: 16px;
    overflow: hidden;
    box-shadow: 0 10px 30px rgba(0,0,0,0.55);
  }
  .card--builder { left: 27px; }
  .card--realty { left: 613px; }

  .brand {
    position: absolute;
    left: 0; width: 250px;
    top: 0; bottom: 40px;
    display: flex; align-items: center; justify-content: center;
    gap: 10px;
  }
  .brand__name {
    font-weight: 700;
    color: var(--blue);
    font-size: 38px;
    letter-spacing: 0.5px;
    white-space: nowrap;
  }
  .card--realty .brand__name { font-weight: 400; font-size: 40px; }
  .brand__dot {
    width: 14px; height: 14px; border-radius: 50%;
    background: var(--red);
    flex: none;
  }

  .divider {
    position: absolute;
    left: 258px; top: 62px;
    width: 1.5px; height: 170px;
    background: linear-gradient(to bottom, rgba(255,255,255,0), var(--divider) 25%, var(--divider) 75%, rgba(255,255,255,0));
  }

  .details {
    position: absolute;
    left: 290px; top: 58px;
  }
  .card--realty .details { top: 40px; }
  .person__name {
    font-weight: 700;
    font-size: 32px;
    line-height: 1;
  }
  .person__first { color: var(--blue); }
  .person__last { color: var(--red); }
  .person__title {
    font-weight: 700;
    font-size: 16px;
    margin: 2px 0 0 14px;
    color: var(--white);
  }
  .contacts {
    list-style: none;
    margin: 12px 0 0 26px;
  }
  .contacts li {
    display: flex; align-items: center; gap: 8px;
    font-size: 15px;
    line-height: 21px;
    white-space: nowrap;
  }
  .icon { width: 13px; height: 13px; flex: none; }
  .icon--dot { width: 11px; height: 11px; border-radius: 50%; background: var(--blue); margin: 0 1px; }

  .address {
    position: absolute;
    left: 330px; bottom: 48px;
    font-size: 16px;
  }

  .bands {
    position: absolute;
    left: 0; bottom: 0;
    width: 560px; height: 40px;
  }
</style>
</head>
<body>

<section class="card card--builder" aria-label="Stone Dorf Design card">
  <div class="brand">
    <span class="brand__dot"></span>
    <span class="brand__name">Stone Dorf</span>
  </div>
  <div class="divider"></div>
  <div class="details">
    <p class="person__name"><span class="person__first">Marek</span> <span class="person__last">Tove</span></p>
    <p class="person__title">Director</p>
    <ul class="contacts">
      <li>
        <svg class="icon" viewBox="0 0 24 24" aria-hidden="true"><path fill="#0b72bf" d="M6.6 10.8a15.1 15.1 0 0 0 6.6 6.6l2.2-2.2a1 1 0 0 1 1-.25 11.4 11.4 0 0 0 3.6.57 1 1 0 0 1 1 1V20a1 1 0 0 1-1 1A17 17 0 0 1 3 4a1 1 0 0 1 1-1h3.5a1 1 0 0 1 1 1c0 1.25.2 2.45.57 3.57a1 1 0 0 1-.25 1z"/></svg>
        5558130467
      </li>
      <li><span class="icon icon--dot"></span>Stonedorf_Bzq</li>
      <li>
        <svg class="icon" viewBox="0 0 24 24" aria-hidden="true"><rect x="2" y="5" width="20" height="14" fill="#0b72bf"/><polyline points="2,5 12,13 22,5" fill="none" stroke="#1e1e22" stroke-width="2"/></svg>
        Stonedorfdev@mailbox.example
      </li>
    </ul>
  </div>
  <svg class="bands" viewBox="0 0 560 40" aria-hidden="true">
    <polygon points="0,22 305,22 285,40 0,40" fill="#e05243"/>
    <polygon points="338,12 560,12 560,40 312,40" fill="#0b72bf"/>
  </svg>
</section>

<section class="card card--realty" aria-label="Marek Tove realty card">
  <div class="brand">
    <span class="brand__name">Marek Tove</span>
  </div>
  <div class="divider"></div>
  <div class="details">
    <p class="person__name"><span class="person__first">Marek</span> <span class="person__last">Tove</span></p>
    <p class="person__title">Director</p>
    <ul class="contacts">
      <li>
        <svg class="icon" viewBox="0 0 24 24" aria-hidden="true"><path fill="#0b72bf" d="M6.6 10.8a15.1 15.1 0 0 0 6.6 6.6l2.2-2.2a1 1 0 0 1 1-.25 11.4 11.4 0 0 0 3.6.57 1 1 0 0 1 1 1V20a1 1 0 0 1-1 1A17 17 0 0 1 3 4a1 1 0 0 1 1-1h3.5a1 1 0 0 1 1 1c0 1.25.2 2.45.57 3.57a1 1 0 0 1-.25 1z"/></svg>
        5558130467
      </li>
      <li><span class="icon icon--dot"></span>marekt</li>
      <li><span class="icon icon--dot"></span>Marek_Bzq_Realtor</li>
      <li>
        <svg class="icon" viewBox="0 0 24 24" aria-hidden="true"><rect x="2" y="5" width="20" height="14" fill="#0b72bf"/><polyline points="2,5 12,13 22,5" fill="none" stroke="#1e1e22" stroke-width="2"/></svg>
        Marek@Marektove.example
      </li>
      <li>
        <svg class="icon" viewBox="0 0 24 24" aria-hidden="true"><g fill="none" stroke="#0b72bf" stroke-width="2"><circle cx="12" cy="12" r="9"/><ellipse cx="12" cy="12" rx="4" ry="9"/><line x1="3" y1="12" x2="21" y2="12"/></g></svg>
        www.marektove.example
      </li>
    </ul>
  </div>
  <p class="address">3847 61 St Nw</p>
  <svg class="bands" viewBox="0 0 560 40" aria-hidden="true">
    <polygon points="0,22 305,22 285,40 0,40" fill="#e05243"/>
    <polygon points="338,12 560,12 560,40 312,40" fill="#0b72bf"/>
  </svg>
</section>

</body>
</html>
```